High-end construction company needs a business card design

We need a modern looking business card that draws people in, is memorable and looks so good people will want to sick it on their fridges.
On the first side what is needed are:
Logo
My name - Tomasz Brelwik
Title - Managing Director
Website - www.varkelt.co.uk
Email - tomasz@varkelt.co.uk
Telephone - 020 5194 6281
Mobile - 07845139072
On the back side was is needed is a list of all the services we provide:
-Kitchen Renovations
-Bathroom Renovations
-House Renovations
-Garage Conversions
-Extensions
-Loft Conversions
-Conservatories
-Carpentry
-Tiling
-Electrical
-Plumbing & Heating
-Bricklaying
-Landscaping
-Decorating
-Plastering
We would like the colours to be the same shades as on the logo with grey or black for the words.
Target Market(s)
Anyone who needs building work done
Contact Information for Business Card
This business card is for a construction company which strives to deliver excellent service and quality.
The look and feel of the card should represent this.
Requirements
Must have
- On the first side what is needed are:
Logo
My name - Tomasz Brelwik
Title - Managing Director
Website - www.varkelt.co.uk
Email - tomasz@varkelt.co.uk
Telephone - 020 5194 6281
Mobile - 07845139072
Nice to have
- Cool looking features

```html
<!DOCTYPE html>
<html lang="en">
<head>
<meta charset="utf-8">
<title>Varkelt Construction Ltd – Business Card</title>
<link rel="stylesheet" href="https://fonts.googleapis.com/css2?family=Michroma&family=Ubuntu:wght@400;700&display=swap">
<style>
  :root {
    --bg: #2a2a2c;
    --green-light: #79c143;
    --green: #5fae3e;
    --green-dark: #3f8a3a;
    --ink: #4a4a4a;
    --white: #ffffff;
    --list-font: "Michroma", sans-serif;
    --text-font: "Ubuntu", sans-serif;
  }
  * { box-sizing: border-box; margin: 0; padding: 0; }
  html, body { width: 1200px; height: 1200px; overflow: hidden; }
  body {
    background: var(--bg);
    display: flex;
    flex-direction: column;
    align-items: center;
    justify-content: center;
    gap: 60px;
  }
  .card {
    position: relative;
    width: 880px;
    height: 503px;
    overflow: hidden;
  }

  /* Back side: services */
  .card-back {
    background: linear-gradient(160deg, var(--green-light) 0%, var(--green) 55%, var(--green-dark) 100%);
    color: var(--white);
  }
  .services {
    position: absolute;
    left: 70px;
    top: 46px;
    list-style: none;
    font-family: var(--list-font);
    font-size: 15.5px;
    line-height: 24.5px;
    letter-spacing: 1px;
  }
  .services li { display: flex; align-items: center; }
  .services li::before {
    content: "";
    width: 8px; height: 8px;
    border-radius: 50%;
    background: var(--white);
    margin-right: 14px;
    flex: none;
  }
  .back-brand {
    position: absolute;
    right: 60px;
    top: 170px;
    text-align: center;
    font-family: var(--list-font);
    color: var(--white);
  }
  .brand-name { font-size: 64px; line-height: 1; letter-spacing: 2px; }
  .brand-sub { font-size: 18px; letter-spacing: 5px; margin-top: 10px; }
  .back-web {
    position: absolute;
    right: 60px;
    bottom: 44px;
    font-family: var(--text-font);
    font-size: 20px;
    letter-spacing: 1.5px;
  }
  .back-web b { font-weight: 700; }

  /* Front side: contact */
  .card-front { background: var(--white); }
  .front-brand {
    position: absolute;
    left: 60px;
    top: 170px;
    width: 400px;
    text-align: center;
    font-family: var(--list-font);
    color: var(--green);
  }
  .front-brand .brand-name { font-size: 56px; }
  .front-brand .brand-sub { font-size: 15px; letter-spacing: 4px; }
  .divider {
    position: absolute;
    left: 490px;
    top: 130px;
    width: 2px;
    height: 210px;
    background: var(--green);
  }
  .contact {
    position: absolute;
    left: 530px;
    top: 140px;
    font-family: var(--text-font);
    color: var(--ink);
  }
  .person-name {
    font-weight: 700;
    font-size: 27px;
    letter-spacing: 1.5px;
    color: var(--green);
    text-transform: uppercase;
  }
  .person-title { font-size: 20px; letter-spacing: 1px; margin-top: 2px; }
  .contact-list { list-style: none; margin-top: 24px; font-size: 21px; letter-spacing: 1px; }
  .contact-list li { display: flex; align-items: center; height: 34px; }
  .contact-list svg { width: 22px; height: 22px; margin-right: 14px; flex: none; }
  .contact-list .accent { color: var(--green); }
  .front-band {
    position: absolute;
    left: 0; right: 0; bottom: 0;
    height: 16px;
    display: flex;
  }
  .front-band .band-dark { flex: 1; background: var(--green-dark); }
  .front-band .band-light { flex: 1; background: var(--green-light); }
</style>
</head>
<body>

  <section class="card card-back" aria-label="Card back: services">
    <ul class="services">
      <li>Kitchen Renovations</li>
      <li>Bathroom Renovations</li>
      <li>House Renovations</li>
      <li>Garage Conversions</li>
      <li>Extensions</li>
      <li>Loft Conversions</li>
      <li>Conservatories</li>
      <li>Carpentry</li>
      <li>Tiling</li>
      <li>Electrical</li>
      <li>Plumbing &amp; Heating</li>
      <li>Bricklaying</li>
      <li>Landscaping</li>
      <li>Decorating</li>
      <li>Plastering</li>
    </ul>
    <div class="back-brand">
      <div class="brand-name">VARKELT</div>
      <div class="brand-sub">CONSTRUCTION LTD</div>
    </div>
    <div class="back-web">www.<b>varkelt</b>.co.uk</div>
  </section>

  <section class="card card-front" aria-label="Card front: contact details">
    <div class="front-brand">
      <div class="brand-name">VARKELT</div>
      <div class="brand-sub">CONSTRUCTION LTD</div>
    </div>
    <div class="divider"></div>
    <div class="contact">
      <div class="person-name">Tomasz Brelwik</div>
      <div class="person-title">Managing Director</div>
      <ul class="contact-list">
        <li>
          <svg viewBox="0 0 24 24" aria-hidden="true"><circle cx="12" cy="12" r="11" fill="#5fae3e"/><path d="M8.5 6.5l2 2-1.2 1.5c.7 1.6 2 2.9 3.6 3.6l1.5-1.2 2 2-1.3 1.6c-3.8-.4-7.2-3.8-7.6-7.6z" fill="#fff"/></svg>
          020 5194 6281
        </li>
        <li>
          <svg viewBox="0 0 24 24" aria-hidden="true"><circle cx="12" cy="12" r="11" fill="#5fae3e"/><rect x="8.5" y="5.5" width="7" height="13" rx="1.5" fill="#fff"/><rect x="9.8" y="7.2" width="4.4" height="8" fill="#5fae3e"/></svg>
          07845139072
        </li>
        <li>
          <svg viewBox="0 0 24 24" aria-hidden="true"><circle cx="12" cy="12" r="11" fill="#5fae3e"/><rect x="6" y="8" width="12" height="8.5" rx="1" fill="#fff"/><path d="M6.5 8.5l5.5 4.2 5.5-4.2" fill="none" stroke="#5fae3e" stroke-width="1.2"/></svg>
          tomasz@varkelt.co.uk
        </li>
        <li>
          <svg viewBox="0 0 24 24" aria-hidden="true"><circle cx="12" cy="12" r="11" fill="#5fae3e"/><g fill="none" stroke="#fff" stroke-width="1.2"><circle cx="12" cy="12" r="6"/><ellipse cx="12" cy="12" rx="2.6" ry="6"/><path d="M6 12h12M7 9h10M7 15h10"/></g></svg>
          www.<span class="accent">varkelt</span>.co.uk
        </li>
      </ul>
    </div>
    <div class="front-band"><span class="band-dark"></span><span class="band-light"></span></div>
  </section>

</body>
</html>
```